New word press website site design

We provide email marketing to aircraft brokers and dealers to assist in finding buyers for their aircraft.

Our target market to purchase our broadcasts are the aircraft sellers – NOT the buyers.

Our target market when sending the email broadcast, are the buyers (end users).

The website should target brokers and our email database targets the buyers.

We do not buy or sell aircraft as a company. We provide email marketing solutions to connect buyers and sellers of aircraft.

Our other site is planelantern.com and will be redesigned soon. Please use it as a reference as far as general scope but they layout can be completely different and should include helicopters only as far as imagery. The colors should be similar as the logos are similar, however we do NOT want both sites to be identical in use of primary color

Plenty of images and sample broadcasts attached to use as needed throughout the site.

Headlines listed below with some text copy.

In the event that we need to add more text, please use standard greek text as a place holder for the purposes of the mockup design.

Need to have a “SUBSCRIBE” button to join our mailing list.

Possible Headlines:

Exclusively Showcasing Rotor Wing Aircraft to the Global Marketplace

Showcasing Pre-Owned Helicopters Available For Sale, Lease, Trade, or Wanted for Acquisition.

Mobile-optimized Email Campaigns that Render Correctly Across all Devices

Targeted worldwide recipients that currently own, operate, or have an interest in rotor wing aircraft

STRONGEST Rotor Wing Database in the Industry

Text/Copy:

HOME
Rotorbay Vista is one of most powerful marketing tools in the industry to utilize in reaching targeted buyers of pre-owned helicopters. Rotorbay Vista provides the rotor wing aircraft market with a fast, effective, and affordable email broadcast solution to utilize in the marketing of Helicopters for sale.

Developed Exclusively to Showcase Rotor Wing Aircraft to the Global marketplace, Rotorbay Vista is a powerful tool designed to maximize leads and accelerate the sales process by providing the ability to reach a global network of Helicopter buyers in a matter of seconds.

DATABASE:

While Rotorbay Vista is delivered to all known broker/dealers, our primary focus is in reaching end users. Our opt-in/opt-out recipient database is updated daily and developed specifically to deliver the latest details on helicopters available for sale or lease to the inboxes of a global network of Helicopter buyers and sellers.

· Helicopter Owners

· Helicopter Operators

· Helicopter Charter Services

· Helicopter Management Companies

· Corporate/Municipal Flight Departments

· Helicopter Pilots

· Senior Aviation Executives

· Wealth Management Firms

· High Net Worth Individuals

· Helicopter Broker/Dealers

Helicopter Tour/Travel Firms

· Off Shore Oil & Gas Production Firms

· Municipalities/Media/Medevac Firms

Our recipient database is continuously updated and developed specifically to reach buyers and sellers of Helicopters. This ensures that your Helicopter will be showcased to the right people. Rotorbay Vista does not broadcast non-rotor wing aircraft and focuses exclusively on the Global Helicopter Market.

Broadcast Design:

Rotorbay Vista broadcast ads are custom designed for you by incorporating your corporate image and branding. Because you have worked hard in developing your corporate image, we strive to maintain it while designing an ad that will showcase your Helicopter to its best advantage. Rotorbay Vista utilizes Mobile-optimized Email Campaigns with Responsive Coding to render correctly across all devices

Once you have approved the design, we schedule the broadcast to be sent on the available date and time you request. The broadcast will link to your website and the results can be immediate. All email leads and replies will go to the email address that you provided.

Pricing:
Create a place holder for 3 Different Broadcast Packages

-Broadcast Package A
-Broadcast Package B
-Broadcast Package C

Target Market(s)

The target market is any person or company that has aircraft for sale. We work with brokers, dealers, and owners to assist in finding buyers for their aircraft using email marketing campaigns (Showcase broadcasts).

Industry/Entity Type

Aviation

Colors
0255a3
00a990

Requirements
Nice to have
• Samples of helicopter for sale broadcast ads in /image gallery/slider

```html
<!DOCTYPE html>
<html lang="en">
<head>
<meta charset="utf-8">
<title>Altivane Media Inc — Rotorbay Vista</title>
<link rel="stylesheet" href="https://fonts.googleapis.com/css2?family=Oswald:wght@500;600&family=Lato:wght@400;700&display=swap">
<style>
  :root {
    --navy: #2c2c80;
    --navy-deep: #23236b;
    --red: #e2182b;
    --white: #ffffff;
    --ink: #1f1f1f;
    --card-shadow: rgba(0, 0, 0, 0.22);
    --rule: #c9c9c9;
  }
  * { margin: 0; padding: 0; box-sizing: border-box; }
  html, body { width: 1200px; height: 3543px; overflow: hidden; }
  body {
    position: relative;
    background: var(--white);
    font-family: "Lato", Arial, sans-serif;
    color: var(--ink);
  }
  .heading {
    font-family: "Oswald", "Arial Narrow", sans-serif;
    font-weight: 600;
    text-transform: uppercase;
    letter-spacing: 0.5px;
  }

  /* Header */
  .site-header { position: absolute; left: 0; top: 0; width: 1200px; height: 208px; }
  .brand {
    position: absolute; left: 31px; top: 92px;
    display: flex; align-items: center; gap: 16px;
    font-size: 52px; line-height: 1; color: var(--navy);
  }
  .brand-mark { width: 22px; height: 22px; background: var(--red); }
  .subscribe {
    position: absolute; left: 947px; top: 52px; width: 222px; height: 90px;
    background: var(--navy); color: var(--white);
    display: flex; align-items: center; justify-content: center;
    font-size: 38px; text-decoration: none;
  }
  .header-rule { position: absolute; left: 0; top: 196px; width: 1200px; height: 12px;
    border-top: 3px solid var(--navy); border-bottom: 3px solid var(--red); }

  /* Hero */
  .hero { position: absolute; left: 0; top: 208px; width: 1200px; height: 690px; }
  .hero-photo {
    position: absolute; inset: 0;
    background:
      radial-gradient(ellipse 55% 30% at 52% 52%, rgba(200, 30, 30, 0.85), rgba(140, 20, 20, 0) 70%),
      linear-gradient(180deg, #0f2238 0%, #1b3a5c 45%, #6a5a52 72%, #2a2a2c 80%, #3a3a3c 100%);
  }
  .hero-title {
    position: absolute; left: 0; top: 70px; width: 1200px; text-align: center;
    color: var(--white); font-size: 44px; font-weight: 500;
  }

  /* About */
  .about { position: absolute; left: 66px; top: 980px; width: 1068px; text-align: center; }
  .section-title { font-size: 52px; color: var(--red); line-height: 1.2; }
  .about p { font-size: 23.5px; line-height: 38px; margin-top: 22px; }
  .about .section-title + p { margin-top: 30px; }

  /* Database */
  .database { position: absolute; left: 0; top: 1490px; width: 1200px; height: 830px; }
  .database .section-title { position: absolute; left: 31px; top: 18px; color: var(--navy); text-align: left; }
  .database-band {
    position: absolute; left: 0; top: 104px; width: 1200px; height: 631px;
    background:
      radial-gradient(ellipse 30% 40% at 62% 55%, rgba(120, 130, 190, 0.35), rgba(0,0,0,0) 70%),
      linear-gradient(180deg, #302f86 0%, #3a3f94 55%, #4b5aa5 100%);
  }
  .database-copy {
    position: absolute; left: 31px; top: 174px; width: 756px;
    color: var(--white); font-size: 23px; line-height: 38px; text-align: justify;
  }
  .database-copy p + p { margin-top: 22px; }
  .scroll-arrow { position: absolute; left: 760px; width: 54px; height: 30px; }
  .scroll-arrow.up { top: 40px; }
  .scroll-arrow.down { top: 770px; }
  .audience-list { position: absolute; left: 831px; top: 7px; width: 338px; list-style: none; }
  .audience-card {
    height: 189px; margin-bottom: 21px; background: var(--white);
    box-shadow: 0 0 14px var(--card-shadow);
    display: flex; flex-direction: column; align-items: center; justify-content: flex-end;
    padding-bottom: 30px; color: var(--navy); font-size: 26px; font-weight: 700;
  }
  .audience-icon { width: 50px; height: 50px; border-radius: 50%; border: 5px solid var(--navy); margin-bottom: 38px; }

  /* Pricing */
  .pricing { position: absolute; left: 66px; top: 2416px; width: 1068px; text-align: center; }
  .pricing p { font-size: 23.5px; line-height: 38px; margin-top: 24px; }
  .packages { position: absolute; left: 31px; top: 2740px; width: 1138px; height: 590px; display: flex; gap: 21px; }
  .package {
    position: relative; flex: 1; background: var(--navy); color: var(--white);
    display: flex; flex-direction: column; align-items: center;
  }
  .package.featured { background: var(--red); }
  .package-name {
    position: relative; margin-top: 14px; width: calc(100% - 28px); height: 82px;
    background: var(--white); color: var(--navy);
    display: flex; align-items: center; justify-content: center; font-size: 31px;
  }
  .package.featured .package-name { color: var(--red); }
  .package-name::after {
    content: ""; position: absolute; left: 50%; bottom: -22px; margin-left: -24px;
    border-left: 24px solid transparent; border-right: 24px solid transparent; border-top: 23px solid var(--white);
  }
  .features { list-style: none; width: calc(100% - 28px); margin-top: 44px; }
  .features li {
    height: 81px; display: flex; align-items: center; justify-content: center;
    font-size: 26px; font-weight: 700; border-bottom: 2px dashed rgba(255,255,255,0.7);
  }
  .features li:first-child { height: 56px; align-items: flex-start; }
  .features li:last-child { border-bottom: none; }
  .get-now {
    margin-top: 10px; width: 156px; height: 64px; border: 3px dashed var(--white);
    display: flex; align-items: center; justify-content: center;
    color: var(--white); text-decoration: none; font-size: 26px; text-transform: uppercase;
  }
  .package.featured .get-now { background: var(--white); color: var(--red); border-style: solid; }

  /* Footer */
  .site-footer { position: absolute; left: 31px; top: 3430px; width: 1138px; border-top: 2px solid var(--rule);
    text-align: center; padding-top: 38px; font-size: 26px; font-weight: 700; }
</style>
</head>
<body>
  <header class="site-header">
    <div class="brand heading"><span class="brand-mark"></span>Altivane Media Inc</div>
    <a class="subscribe heading" href="#">Subscribe</a>
    <div class="header-rule"></div>
  </header>

  <section class="hero">
    <div class="hero-photo" role="img" aria-label="Red helicopter parked on a tarmac at dusk"></div>
    <h1 class="hero-title heading">Strongest Rotor Wing Database in the Industry</h1>
  </section>

  <section class="about">
    <h2 class="section-title heading">About Altivane Media Inc</h2>
    <p>Rotorbay Vista is one of most powerful marketing tools in the industry to utilize in reaching targeted buyers of pre-owned helicopters. Rotorbay Vista provides the rotor wing aircraft market with a fast, effective, and affordable email broadcast solution to utilize in the marketing of Helicopters for sale.</p>
    <p>Developed Exclusively to Showcase Rotor Wing Aircraft to the Global marketplace, Rotorbay Vista is a powerful tool designed to maximize leads and accelerate the sales process by providing the ability to reach a global network of Helicopter buyers in a matter of seconds.</p>
  </section>

  <section class="database">
    <div class="database-band" role="img" aria-label="Faint helicopter photo under a deep blue overlay"></div>
    <h2 class="section-title heading">Database</h2>
    <div class="database-copy">
      <p>While Rotorbay Vista is delivered to all known broker/dealers, our primary focus is in reaching end users.</p>
      <p>Our opt-in/opt-out recipient database is updated daily and developed specifically to deliver the latest details on helicopters available for sale or lease to the inboxes of a global network of Helicopter buyers and sellers.</p>
      <p>Our recipient database is continuously updated and developed specifically to reach buyers and sellers of Helicopters. This ensures that your Helicopter will be showcased to the right people. Rotorbay Vista does not broadcast non-rotor wing aircraft and focuses exclusively on the Global Helicopter Market.</p>
    </div>
    <svg class="scroll-arrow up" viewBox="0 0 54 30" aria-hidden="true"><polyline points="2,28 27,3 52,28" fill="none" stroke="var(--navy)" stroke-width="3"/></svg>
    <svg class="scroll-arrow down" viewBox="0 0 54 30" aria-hidden="true"><polyline points="2,2 27,27 52,2" fill="none" stroke="var(--navy)" stroke-width="3"/></svg>
    <ul class="audience-list">
      <li class="audience-card"><span class="audience-icon"></span>Helicopter Owners</li>
      <li class="audience-card"><span class="audience-icon"></span>Helicopter Operators</li>
      <li class="audience-card"><span class="audience-icon"></span>Helicopter Charter Services</li>
      <li class="audience-card"><span class="audience-icon"></span>Helicopter Broker/Dealers</li>
    </ul>
  </section>

  <section class="pricing">
    <h2 class="section-title heading">Pricing</h2>
    <p>Rotorbay Vista is one of most powerful marketing tools in the industry to utilize in reaching targeted buyers of pre-owned helicopters.</p>
  </section>

  <div class="packages">
    <article class="package">
      <h3 class="package-name">Broadcast Package A</h3>
      <ul class="features"><li>Nemo enim ipsam</li><li>voluptatem quia voluptas</li><li>sit aspernatur aut odit</li><li>aut fugit, sed quia</li></ul>
      <a class="get-now" href="#">Get Now</a>
    </article>
    <article class="package featured">
      <h3 class="package-name">Broadcast Package B</h3>
      <ul class="features"><li>Nemo enim ipsam</li><li>voluptatem quia voluptas</li><li>sit aspernatur aut odit</li><li>aut fugit, sed quia</li></ul>
      <a class="get-now" href="#">Get Now</a>
    </article>
    <article class="package">
      <h3 class="package-name">Broadcast Package C</h3>
      <ul class="features"><li>Nemo enim ipsam</li><li>voluptatem quia voluptas</li><li>sit aspernatur aut odit</li><li>aut fugit, sed quia</li></ul>
      <a class="get-now" href="#">Get Now</a>
    </article>
  </div>

  <footer class="site-footer">Copyrights @ 2018 Altivane Media Inc. All Rights Reserved.</footer>
</body>
</html>
```